Website redesign www.marigoldlawpc.com law firm site

Need to redesign the website that I currently have to look more modern and professional. Would also like to be able to make updates and post without having a huge hassle. See current www.marigoldlawpc.com. I just think that it looks very immature and it's very templated there's no ability for me to make posts or Add links or anything like that

Target Market(s)

California people looking for a powerhouse attorney in

Industry/Entity Type

Legal

Number of Pages Required

3 page

Font styles to use
Serif
Sans Serif

Colors
ec1f27
000000
ffffff

Requirements
Must have
• Must be mobile friendly. Must look professional and have ability to post links to other websites. Must have ability to post blogs or articles. Would like to be able to read my FeeTrove account and also have the ability to upload forms for people to download
Nice to have
• Simple design easy to use and not cluttered with too much text

```html
<!DOCTYPE html>
<html lang="en">
<head>
<meta charset="utf-8">
<title>Marigold Law P.C.</title>
<link href="https://fonts.googleapis.com/css2?family=Cinzel:wght@400;700&family=Open+Sans:wght@400;600;700&display=swap" rel="stylesheet">
<style>
:root{
  --red:#ec1f27;
  --black:#000;
  --ink:#222;
  --grey-text:#555;
  --light:#f0f0f0;
  --white:#fff;
  --placeholder:#c9c9c9;
  --serif:'Cinzel', Georgia, serif;
  --sans:'Open Sans', Arial, sans-serif;
}
*{box-sizing:border-box;margin:0;padding:0}
html,body{width:1200px;height:2483px;overflow:hidden}
body{position:relative;background:var(--white);font-family:var(--sans);color:var(--ink)}
.abs{position:absolute}

/* header */
.site-header{position:absolute;top:0;left:0;width:1200px;height:80px;background:linear-gradient(#f4f4f4,#e9e9e9)}
.brand{position:absolute;left:177px;top:14px;text-align:center;font-family:var(--serif);color:var(--red)}
.brand .name{font-size:30px;letter-spacing:1px;line-height:1}
.brand .sub{font-size:13px;border-top:1px solid var(--red);margin-top:3px;padding-top:1px}
.header-contact{position:absolute;left:720px;top:24px;font-size:12.5px;line-height:16px;color:#333}
.header-contact .phone-icon{position:absolute;left:-24px;top:2px}
.social{position:absolute;left:938px;top:26px;display:flex;gap:10px}
.social span{width:26px;height:26px;border-radius:4px;background:#555}

/* nav */
.main-nav{position:absolute;top:80px;left:0;width:1200px;height:33px;background:linear-gradient(#2a2a2a,#0b0b0b)}
.main-nav ul{list-style:none}
.main-nav li{position:absolute;top:0;height:33px;text-align:center;white-space:nowrap;font-family:var(--serif);font-size:12.5px;font-weight:700;color:var(--white);line-height:33px;letter-spacing:.5px}
.main-nav li.active{background:var(--red)}
.main-nav .sep{position:absolute;top:11px;width:1px;height:11px;background:#555}

/* hero */
.hero{position:absolute;top:113px;left:0;width:1200px;height:458px;background:linear-gradient(120deg,#4a5566 0%,#7a8392 35%,#b8b2ab 60%,#9b948c 100%)}
.hero-caption{position:absolute;left:160px;top:160px;background:rgba(20,20,20,.82);padding:8px 14px 10px;color:var(--white);font-family:var(--serif)}
.hero-caption .small{font-size:19px;letter-spacing:1px}
.hero-caption .big{font-size:37px;line-height:1}
.btn-red{display:inline-block;background:var(--red);color:var(--white);font-family:var(--serif);font-size:12.5px;font-weight:700;padding:8px 14px;letter-spacing:.5px;white-space:nowrap}
.hero .btn-red{position:absolute;left:160px;top:244px}
.arrow-tab{position:absolute;top:183px;width:30px;height:86px;background:rgba(220,220,220,.6)}
.thumbs{position:absolute;left:520px;top:433px;display:flex;gap:4px;background:#fff;padding:3px}
.thumbs span{width:52px;height:34px;background:#8b95a5}
.thumbs span:nth-child(2){background:#c7b8b0}
.thumbs span:nth-child(3){background:#7c8a7a}

/* headings */
.section-title{position:absolute;left:0;width:1200px;text-align:center;font-family:var(--serif);font-size:29px;color:var(--ink);letter-spacing:.5px}
.section-title em{font-style:normal;color:var(--red)}
.section-title::after{content:"";display:block;width:80px;height:2px;background:#999;margin:10px auto 0}

/* welcome */
.welcome-text{position:absolute;left:166px;top:688px;width:868px;text-align:center;font-size:12.5px;line-height:26.5px;color:var(--grey-text)}
.btn-outline{display:inline-block;border:2px solid var(--ink);color:var(--ink);font-family:var(--serif);font-size:12.5px;font-weight:700;padding:6px 12px;white-space:nowrap}

/* practice */
.practice{position:absolute;top:890px;left:0;width:1200px;height:406px;background:linear-gradient(90deg,#e8e6e4,#f4f3f2 50%,#e3e5e8)}
.practice-item{position:absolute;width:280px;font-size:11.5px;color:#555;line-height:16px}
.practice-item h3{font-family:var(--serif);font-size:15px;color:var(--ink);font-weight:700;margin-bottom:2px}
.practice-item.left{text-align:right}
.practice-item svg{position:absolute;top:0}
.pillar{position:absolute;left:570px;top:103px;width:60px;height:257px;background:var(--white);display:flex;align-items:center;justify-content:center}
.pillar span{transform:rotate(-90deg);white-space:nowrap;font-family:var(--serif);font-size:31px;color:var(--ink)}
.pillar em{font-style:normal;color:var(--red)}
.connector{position:absolute;height:1px;background:#bbb;width:200px}

/* testimonials */
.testimonial{position:absolute;top:1432px;width:300px}
.testimonial .avatar{position:absolute;left:0;top:0;width:60px;height:60px;border-radius:50%;background:#b9a393;border:2px solid #ddd}
.testimonial p{margin-left:76px;font-size:12px;line-height:20px;color:#555;letter-spacing:.3px}
.testimonial .q{color:#bbb;font-family:Georgia,serif;font-size:26px;line-height:0;vertical-align:-8px}
.testimonial h4{margin-left:66px;margin-top:8px;font-family:var(--serif);font-size:13px;font-weight:700}

/* ratings */
.ratings{position:absolute;top:1688px;left:0;width:1200px;height:166px;background:var(--light)}
.ribbon{position:absolute;left:162px;top:-6px;background:var(--red);color:var(--white);font-family:var(--serif);font-size:22px;padding:6px 16px;transform:skewX(-4deg);letter-spacing:.5px}
.ratings p{position:absolute;left:162px;top:62px;width:300px;font-size:11px;line-height:18.5px;color:#555}
.badge-divider{position:absolute;top:70px;width:1px;height:50px;background:#c8c8c8}
.badge{position:absolute;background:var(--placeholder)}

/* contact */
.contact{position:absolute;top:1854px;left:0;width:1200px;height:629px;background:linear-gradient(#2b3644,#141c27 70%,#0c1118)}
.contact .section-title{color:var(--white);top:33px}
.contact .section-title::after{background:#aaa}
.contact-card{position:absolute;left:257px;top:146px;width:685px;height:383px;background:rgba(210,30,38,.72)}
.plane{position:absolute;left:573px;top:126px;width:52px;height:52px;border-radius:50%;background:var(--white);display:flex;align-items:center;justify-content:center}
.contact-info{position:absolute;left:0;top:45px;width:685px;text-align:center;color:var(--white);font-size:11px;font-weight:700;line-height:22px}
.field{position:absolute;background:rgba(255,255,255,.22);color:var(--white);font-size:11px;font-weight:700;padding:8px}
.btn-send{position:absolute;left:273px;top:331px;border:2px solid var(--white);color:var(--white);font-family:var(--serif);font-size:12.5px;font-weight:700;padding:6px 14px;white-space:nowrap}
.footer-nav{position:absolute;top:546px;left:0;width:1200px;text-align:center;color:var(--white);font-size:10.5px;font-weight:600;letter-spacing:.5px}
.footer-nav span{margin:0 20px}
.footer-bar{position:absolute;top:579px;left:0;width:1200px;height:50px;border-top:1px solid rgba(255,255,255,.25)}
.footer-bar p{position:absolute;left:163px;top:15px;color:var(--white);font-size:11px;font-weight:600}
.footer-social{position:absolute;left:935px;top:11px;display:flex;gap:10px}
.footer-social span{width:26px;height:26px;border-radius:50%;border:1.5px solid var(--red)}
</style>
</head>
<body>

<header class="site-header">
  <div class="brand"><div class="name">Marigold Law</div><div class="sub">P.C</div></div>
  <div class="header-contact">
    <svg class="phone-icon" width="14" height="22" viewBox="0 0 14 22"><rect x="1" y="1" width="12" height="20" rx="2" fill="#9a9a9a"/><rect x="3" y="4" width="8" height="12" fill="#ddd"/></svg>
    (530) 555-0148<br>dana@marigoldlawgroup.com
  </div>
  <div class="social" aria-label="Social links"><span></span><span></span><span></span></div>
</header>

<nav class="main-nav">
  <ul>
    <li class="active" style="left:161px;width:116px">Home</li>
    <li style="left:296px;width:150px">Attorney Profile</li>
    <li style="left:478px;width:150px">Practice Areas</li>
    <li style="left:663px;width:150px">Client Reviews</li>
    <li style="left:814px;width:100px">Links</li>
    <li style="left:933px;width:120px">Contact Us</li>
  </ul>
  <span class="sep" style="left:467px"></span><span class="sep" style="left:640px"></span>
  <span class="sep" style="left:812px"></span><span class="sep" style="left:918px"></span>
</nav>

<section class="hero" role="img" aria-label="Photo of handcuffed hands resting on jeans">
  <div class="arrow-tab" style="left:0"></div>
  <div class="arrow-tab" style="right:0"></div>
  <div class="hero-caption"><div class="small">The Greatest Firm</div><div class="big">YOU CAN TRUST</div></div>
  <span class="btn-red">MORE INFO ▸</span>
  <div class="thumbs"><span role="img" aria-label="Slide thumbnail"></span><span role="img" aria-label="Slide thumbnail"></span><span role="img" aria-label="Slide thumbnail"></span></div>
</section>

<h2 class="section-title" style="top:628px">Welcome To &nbsp;<em>Marigold Law P.C.</em></h2>
<p class="welcome-text">Marigold Law P.C. is owned by Dana L. Marigold, a dedicated and caring professional who uses her broad range of skills as a California lawyer to bring consumers and business owners exceptionally strong legal representation that achieves best results. She works with people from across the northern region of California, from the Northern border to the Central Valley region. They bring her legal concerns and problems that occur in many areas of law, including Real Estate, Family law, Business Law, Bankruptcy, Criminal Law and Civil Litigation.</p>
<div class="abs" style="top:811px;left:460px;display:flex;gap:8px">
  <span class="btn-red">READ MORE ▸</span>
  <span class="btn-outline">DOWNLOAD FORM ▸</span>
</div>

<section class="practice" role="img" aria-label="Soft photo of a hand signing papers near a model house">
  <h2 class="section-title" style="top:30px">Practice <em>Areas</em></h2>

  <div class="connector" style="left:400px;top:145px"></div><div class="connector" style="left:600px;top:145px"></div>
  <div class="connector" style="left:400px;top:228px"></div><div class="connector" style="left:600px;top:228px"></div>
  <div class="connector" style="left:400px;top:311px"></div><div class="connector" style="left:600px;top:311px"></div>

  <div class="pillar"><span>MARIGOLD <em>LAW</em></span></div>

  <div class="practice-item left" style="left:122px;top:120px"><h3>Business Law</h3>Lorem ipsum dolor sit onsectetue wisi<br>enim ad minim veniam,...
    <svg style="right:-72px" width="46" height="40" viewBox="0 0 46 40" fill="none" stroke="#ec1f27" stroke-width="2"><rect x="3" y="10" width="40" height="26" rx="2"/><path d="M16 10V5h14v5M3 20h40"/></svg></div>
  <div class="practice-item left" style="left:122px;top:203px"><h3>Real Estate Law</h3>Lorem ipsum dolor sit onsectetue wisi<br>enim ad minim veniam, ...
    <svg style="right:-72px" width="46" height="40" viewBox="0 0 46 40" fill="none" stroke="#ec1f27" stroke-width="2"><path d="M5 20L23 4l18 16M10 16v20h26V16"/><rect x="18" y="20" width="10" height="10"/></svg></div>
  <div class="practice-item left" style="left:122px;top:286px"><h3>Bankruptcy</h3>Lorem ipsum dolor sit onsectetue wisi<br>enim ad minim veniam,...
    <svg style="right:-72px" width="46" height="44" viewBox="0 0 46 44" fill="none" stroke="#ec1f27" stroke-width="2"><path d="M16 10h14l-4 7c9 4 12 12 10 22H10C8 29 11 21 20 17z"/><path d="M18 4h10"/></svg></div>

  <div class="practice-item" style="left:804px;top:120px"><h3>Family Law</h3>Lorem ipsum dolor sit onsectetue wisi<br>enim ad minim veniam,...
    <svg style="left:-72px" width="46" height="40" viewBox="0 0 46 40" fill="none" stroke="#ec1f27" stroke-width="2"><circle cx="15" cy="7" r="4"/><circle cx="31" cy="7" r="4"/><path d="M10 38V14h10v24M26 38V14h10v24"/></svg></div>
  <div class="practice-item" style="left:804px;top:203px"><h3>Criminal Law</h3>Lorem ipsum dolor sit onsectetue wisi<br>enim ad minim veniam, ...
    <svg style="left:-72px" width="56" height="40" viewBox="0 0 56 40" fill="none" stroke="#ec1f27" stroke-width="2"><circle cx="15" cy="24" r="11"/><circle cx="41" cy="24" r="11"/><path d="M24 17c3-4 5-4 8 0"/></svg></div>
  <div class="practice-item" style="left:804px;top:286px"><h3>Civil Litigation</h3>Lorem ipsum dolor sit onsectetue wisi<br>enim ad minim veniam,...
    <svg style="left:-72px" width="46" height="40" viewBox="0 0 46 40" fill="none" stroke="#ec1f27" stroke-width="2"><path d="M10 12l10-8 6 7-10 8zM18 15l16 16M6 37h22"/></svg></div>
</section>

<h2 class="section-title" style="top:1342px">What People Say <em>About Us?</em></h2>

<div class="testimonial" style="left:165px"><div class="avatar" role="img" aria-label="Client portrait"></div>
  <p><span class="q">“</span> Mattis porttitor nulla, eget eleif end metus gravida id . Nune sollicit udin nune at tellus pretium a pulvinar purus. Mattis porttitor null, eget eleifend mentus. <span class="q">”</span></p><h4>LOREM ISPUM</h4></div>
<div class="testimonial" style="left:465px"><div class="avatar" role="img" aria-label="Client portrait"></div>
  <p><span class="q">“</span> Mattis porttitor nulla, eget eleif end metus gravida id . Nune sollicit udin nune at tellus pretium a pulvinar purus. Mattis porttitor null, eget eleifend mentus. <span class="q">”</span></p><h4>LOREM ISPUM</h4></div>
<div class="testimonial" style="left:763px"><div class="avatar" role="img" aria-label="Client portrait"></div>
  <p><span class="q">“</span> Mattis porttitor nulla, eget eleif end metus gravida id . Nune sollicit udin nune at tellus pretium a pulvinar purus. Mattis porttitor null, eget eleifend mentus. <span class="q">”</span></p><h4>LOREM ISPUM</h4></div>

<span class="btn-outline abs" style="left:540px;top:1597px">VIEW MORE ▸</span>

<section class="ratings">
  <div class="ribbon">RATINGS &amp; REVIEWS</div>
  <p>Alore eu feugiat nulla facilisis at vero eros e accumsan et iusto odio dignissim qui blandit praesent luptatum zzril delenit augueguat nulla facilisi.</p>
  <div class="badge" role="img" aria-label="Review site rating badge" style="left:524px;top:58px;width:78px;height:78px;border-radius:8px"></div>
  <div class="badge-divider" style="left:644px"></div>
  <div class="badge" role="img" aria-label="State bar membership badge" style="left:684px;top:58px;width:78px;height:78px;border-radius:50%"></div>
  <div class="badge-divider" style="left:800px"></div>
  <div class="badge" role="img" aria-label="Lawyer directory listing badge" style="left:838px;top:72px;width:200px;height:50px;border-radius:4px"></div>
</section>

<section class="contact" role="img" aria-label="Silhouettes of business people shaking hands in an office">
  <h2 class="section-title">Contact <em>Us</em></h2>
  <div class="contact-card">
    <div class="contact-info">Marigold Law, P.C. Office 410 Orchard Avenue Suite 200 Chico, CA 95926<br>dana@marigoldlawgroup.com<br>(530) 555-0148</div>
    <div class="field" style="left:40px;top:143px;width:297px;height:34px">Name</div>
    <div class="field" style="left:344px;top:143px;width:300px;height:34px">Email</div>
    <div class="field" style="left:40px;top:183px;width:604px;height:120px">Message</div>
    <span class="btn-send">SEND MESSAGE ▸</span>
  </div>
  <div class="plane"><svg width="26" height="24" viewBox="0 0 26 24" fill="none" stroke="#222" stroke-width="1.8"><path d="M2 11L24 2l-6 20-6-8zM12 14l12-12"/></svg></div>
  <div class="footer-nav"><span>HOME</span>|<span>ATTORNEY PROFILE</span>|<span>PRACTICE AREAS</span>|<span>CLIENT REVIEWS</span>|<span>LINKS</span>|<span>CONTACT US</span></div>
  <div class="footer-bar">
    <p>Copyright © 2016 - Marigoldlawpc | All Rights Reserved</p>
    <div class="footer-social"><span></span><span></span><span></span></div>
  </div>
</section>

</body>
</html>
```